A5 Patient Information Booklet (Chiropractic Clinic) 4-8 pages

Here’s a polished, professional rewrite of your full brief and content, with clearer structure, corrected language, and a premium tone:

---

**Project Title:** Premium Patient Information Brochure (Chiropractic & Wellness Clinic)

---

### **Overview**

We are a health and wellness clinic seeking a premium, high-end patient information brochure to provide following a patient’s initial consultation and first treatment.

The purpose of this booklet is to:

* Reinforce trust and professionalism
* Help patients understand what to expect next
* Encourage adherence to care recommendations
* Position the clinic as calm, expert-led, and results-driven

---

### **Format**

* 4–8 page booklet (A5 or similar size)
* Print-ready and digital versions required

---

### **Target Audience**

Patients who have just completed their initial consultation and may have begun treatment. They may already be experiencing physical or mental changes, so the brochure should guide, reassure, and educate them on what comes next.

---

### **Tone & Style**

* Premium, calm, and reassuring
* Modern wellness aesthetic (not overly clinical)
* Clean layout with minimal clutter
* Soft, neutral colour palette (whites, creams, muted greens, soft blues)
* Elegant typography (e.g. Montserrat / Lato)
* High-end, trustworthy, and professional feel

---

### **Key Messages**

#### 1. Listen to Your Body

Patients may feel different after treatment. Reassure them that this is normal and part of the healing process.

#### 2. Post-Treatment Advice

* Stay well hydrated
* Rest if needed
* Avoid overexertion if the body requires recovery

#### 3. Healing is a Journey (Core Concept)

A strong visual metaphor of a **“road to recovery”** or **journey** should be central to the design.

This journey should clearly illustrate three phases:

* **Phase 1: Initial Care (Weeks 1–6)**
Focus: Reducing pain/discomfort, calming the body, and initiating response to treatment

* **Phase 2: Corrective Care (Weeks 6–12)**
Focus: Addressing underlying issues, improving function, and creating lasting change

* **Phase 3: Wellness / Maintenance (Ongoing)**
Focus: Maintaining progress, preventing relapse, and supporting long-term wellbeing

**Important:**

* Emphasise that this is not a quick fix
* Progress requires time and consistency
* Each patient follows an individualised care plan
* The journey should feel structured, positive, and achievable

#### 4. Personalised Care

Reinforce that every treatment plan is tailored specifically to the individual.

#### 5. Professional Reassurance

Patients should feel confident they are in expert hands and supported throughout their journey.

---

### **Design Direction**

* Use imagery that reflects calmness, progression, and wellness (e.g. pathways, nature, soft gradients)
* Avoid generic stock imagery
* **Only use original clinic images from website and social media**
* Prioritise white space and clarity
* Aim for a luxury spa/medical hybrid aesthetic

---

## **Content Structure (Page-by-Page)**

### **Front Cover**

* Clean, minimal, premium design
* Clinic branding

---

### **Page 1: Patient Case Summary**

**Title:** *Welcome to Fernwell Spine Studio*

Thank you for choosing Fernwell Spine Studio.

This booklet is designed to guide you through:

* What we found during your initial consultation
* Your personalised recommended treatment plan
* Your road to recovery
* Long-term wellness care
* Why we take the approach we do

---

### **Page 2: Your Care Journey**

**Stage 1: Your Initial Consultation**

Today we completed a comprehensive assessment of your health and function, including:

* Full case history and discussion of your symptoms and goals
* Orthopaedic and neurological testing
* Postural and movement assessment
* Initial treatment (where appropriate)

**What this tells us:**

* How your body is currently functioning
* Where areas of stress or dysfunction may be present
* The most appropriate and effective path forward for your care

---

### **Page 3: Your Suggested Treatment Plan**

Based on today’s findings, your recommended care plan is:

**______ treatments over ______ weeks**

This should be viewed alongside your *Road to Recovery* to help you understand what to expect.

We have also discussed:

* Expected timelines for improvement
* Available payment options

**After Treatment:**
It is common to feel different following treatment. This is a normal response as your body begins to adapt and respond.

We recommend:

* Staying well hydrated
* Allowing time for rest and recovery
* Avoiding overexertion if your body feels it needs it

---

### **Page 4: What to Expect Next**

Healing is not always linear—it is a process that occurs over time.

Your care will typically progress through the following stages:

* **Relief Care**
Focused on reducing discomfort and calming the body

* **Corrective Care**
Focused on addressing underlying issues and improving function
(This phase may include prescribed exercises)

* **Maintenance / Wellness Care**
Focused on sustaining progress, preventing recurrence, and supporting long-term health

---

### **Page 5: Understanding Chiropractic Care**

**What is Chiropractic?**
Chiropractic care focuses on the relationship between the spine, nervous system, and overall body function.

By improving spinal movement and alignment, chiropractic care helps support the nervous system, allowing the body to function and heal more effectively.

**About Fernwell Spine Studio**
At Fernwell Spine Studio, our approach is centred around personalised, patient-focused care. We aim to not only relieve symptoms but to address underlying causes and support long-term wellbeing.

---

### **Back Page**

* Clinic contact details
* Website
* Social media icons/handles

**Closing Message:**
“A healthier, stronger you—supported every step of the way.”

---

### **Deliverables**

* Print-ready PDF
* Editable source files

---

### **Additional Notes**

* The brochure should feel valuable and worth keeping
* Encourage long-term care in a subtle, non-pushy way
* Maintain clarity, readability, and strong visual hierarchy
* Balance professionalism with warmth and approachability

---

If you’d like, I can also turn this into **actual brochure copy (fully written, patient-facing text)** or help you refine it further for a designer.

Existing patients who want to feel better and look after themselves that is given after their initil consultation appointment

Chiropractic, wellness, health

• Montserrat or Lato

0094D4
00A9DD
6FCCEA
C7EBF8
E9F6FB
00AB8E
00BBA5
67D7C9
C6EFE9
E9F9F6
6B429C
8869AF
B7A5CE
E3DAEB
F3F0F8

• my own photos, look premium wellness, be clear and simple to understand for patients journey or what to expect next and over time
• USe my social media/website for ideas
• generic photos and images

```html
<!DOCTYPE html>
<html lang="en">
<head>
<meta charset="utf-8">
<title>Fernwell Spine Studio – Patient Care Journey Booklet</title>
<link href="https://fonts.googleapis.com/css2?family=Lato:wght@300;400;700;900&family=Playfair+Display:wght@400;500&family=Roboto:wght@400;500&display=swap" rel="stylesheet">
<style>
  :root{
    --board:#3a3a3a;
    --white:#ffffff;
    --teal:#14a59e;
    --teal-deep:#0f9990;
    --teal-text:#17a7a0;
    --pink:#ef72b8;
    --purple:#ab92d6;
    --blue:#6fb1e7;
    --ink:#2c2c2c;
    --body:#555a5e;
    --soft:#f4f6f7;
  }
  *{box-sizing:border-box;margin:0;padding:0}
  html,body{width:971px;height:1200px;overflow:hidden}
  body{background:var(--board);font-family:'Lato',sans-serif;position:relative;color:var(--body)}
  .page{position:absolute;width:386px;height:500px;background:var(--white);overflow:hidden}
  .page--cover{left:70px;top:69px}
  .page--recovery{left:515px;top:69px}
  .page--first-visit{left:70px;top:632px}
  .page--continuing{left:515px;top:632px}
  .abs{position:absolute}
  .fill{position:absolute;left:0;top:0}

  /* cover */
  .brand-mark{position:absolute;left:279px;top:15px;width:56px;height:56px;border-radius:50%;border:2px solid var(--purple)}
  .brand-name{position:absolute;left:246px;width:140px;top:75px;text-align:center;font-size:10px;font-weight:700;color:var(--ink);letter-spacing:.2px}
  .brand-tag{position:absolute;left:246px;width:140px;top:89px;text-align:center;font-size:5.3px;color:var(--teal-text);letter-spacing:1.2px}
  .cover-title{position:absolute;left:0;width:386px;top:367px;text-align:center;color:var(--white);font-weight:700;font-size:20.5px;line-height:21.5px;letter-spacing:-.2px}
  .cover-intro{position:absolute;left:40px;width:306px;top:414px;text-align:center;color:var(--white);font-size:7.2px;line-height:12px}
  .field{position:absolute;color:var(--white);font-size:7.4px;white-space:nowrap}
  .blank{display:inline-block;border-bottom:1px dashed rgba(255,255,255,.85);height:7px;vertical-align:baseline}
  .plan-pill{position:absolute;left:0;top:465px;width:110px;height:20px;background:var(--white);border-radius:0 10px 10px 0;color:var(--teal-text);font-size:7.4px;line-height:20px;padding-left:13px}

  /* recovery page */
  .chart-card{position:absolute;left:59px;top:173px;width:271px;height:157px;border-radius:7px;background:var(--white);box-shadow:0 2px 8px rgba(0,0,0,.25);overflow:hidden}
  .chart-band{position:absolute;left:0;top:0;width:26px;height:157px;background:var(--teal)}
  .chart-band-title{position:absolute;left:17px;top:143px;transform:rotate(-90deg);transform-origin:0 0;color:var(--white);font-weight:900;font-size:12.5px;white-space:nowrap;line-height:1}
  .chart-graphic{position:absolute;left:26px;top:0;width:245px;height:157px;background:linear-gradient(90deg,#fdeee3 0%,#fff6d9 45%,#e4f5ec 100%)}
  .welcome-copy{position:absolute;left:40px;width:306px;top:348px;text-align:center;font-size:7.6px;line-height:14.2px;color:var(--body);font-weight:400}
  .welcome-tagline{position:absolute;left:0;width:386px;top:405px;text-align:center;font-size:7.6px;color:var(--teal-text);font-weight:700}

  /* footer band */
  .footer-band{position:absolute;left:0;bottom:0;width:386px;height:140px}
  .footer-title{position:absolute;left:0;width:386px;text-align:center;color:var(--white);font-weight:700;font-size:9px;line-height:10.5px}
  .footer-line{position:absolute;left:0;width:386px;top:484px;text-align:center;color:var(--white);font-size:7px}
  .chat-badge{position:absolute;left:182px;top:432px;width:22px;height:22px;border-radius:50%;background:var(--white);box-shadow:0 1px 3px rgba(0,0,0,.2)}

  /* first visit page */
  .section-title{position:absolute;color:var(--teal-text);font-weight:700;font-size:9.6px;letter-spacing:-.1px;line-height:11px}
  .section-copy{position:absolute;font-size:7.5px;line-height:11.5px;color:var(--body);font-weight:400}
  .justify{text-align:justify}
  .step-card{position:absolute;width:163px;height:43px;border-radius:22px;background:var(--white);box-shadow:0 1px 6px rgba(0,0,0,.14)}
  .step-icon{position:absolute;width:24px;height:24px;border-radius:50%;background:var(--pink)}
  .step-title{position:absolute;color:var(--pink);font-size:7px;font-weight:700;letter-spacing:.1px}
  .step-copy{position:absolute;font-size:6.2px;line-height:10px;color:var(--body);width:120px}

  /* continuing page */
  .bullets{position:absolute;list-style:none;font-size:7.4px;color:var(--body)}
  .bullets li{position:relative;height:13px;line-height:13px;padding-left:11px}
  .bullets li::before{content:"";position:absolute;left:0;top:3.5px;width:6px;height:6px;border-radius:50%;background:var(--pink)}
  .strong-line{position:absolute;font-size:7.3px;font-weight:700;color:var(--ink)}
  .journey-pill{position:absolute;left:0;top:140px;width:386px;height:164px;border-radius:90px/82px;background:linear-gradient(90deg,#f27fbf 0%,#c99ad6 48%,#6fb3e8 100%)}
  .journey-title{position:absolute;left:0;width:386px;top:16px;text-align:center;font-family:'Playfair Display',serif;color:var(--white);font-size:12.3px;letter-spacing:.3px;font-weight:400}
  .journey-sub{position:absolute;left:0;width:386px;top:32px;text-align:center;font-family:'Roboto',sans-serif;color:var(--white);font-size:6.2px}
  .phase{position:absolute;top:41px;width:96px;text-align:center;font-family:'Roboto',sans-serif;color:var(--white)}
  .phase-icon{width:28px;height:28px;margin:0 auto;border-radius:50%;background:var(--white);display:flex;align-items:center;justify-content:center}
  .phase-name{margin-top:9px;font-size:6.6px;font-weight:500}
  .phase-focus{margin:4px auto 0;width:65px;height:15px;line-height:15px;border-radius:8px;background:var(--teal);font-size:5.6px}
  .phase-copy{margin-top:5px;font-size:5.2px;line-height:8.5px;font-weight:500}
</style>
</head>
<body>

<!-- COVER -->
<section class="page page--cover">
  <svg class="fill" width="386" height="500" role="img" aria-label="Photo: chiropractor showing a spine model to a patient holding her lower back">
    <defs>
      <linearGradient id="coverPhoto" x1="0" y1="0" x2="1" y2="1">
        <stop offset="0" stop-color="#d9d5d2"/>
        <stop offset=".45" stop-color="#c7cdd3"/>
        <stop offset="1" stop-color="#9fb6c4"/>
      </linearGradient>
    </defs>
    <path d="M0,0 H246 V116 H386 V420 H0 Z" fill="url(#coverPhoto)"/>
  </svg>
  <div class="brand-mark"></div>
  <div class="brand-name">FERNWELL SPINE STUDIO</div>
  <div class="brand-tag">CHIROPRACTIC &amp; WELLNESS</div>

  <svg class="fill" width="386" height="500">
    <defs>
      <linearGradient id="arcCover" x1="0" x2="1" y1="0" y2="0">
        <stop offset="0" stop-color="#ef72b8"/>
        <stop offset=".5" stop-color="#ab92d6"/>
        <stop offset="1" stop-color="#6fb1e7"/>
      </linearGradient>
    </defs>
    <path d="M0,404 Q193,236 386,404 L386,500 L0,500 Z" fill="url(#arcCover)"/>
    <path d="M0,410 Q193,250 386,410 L386,500 L0,500 Z" fill="var(--teal)"/>
    <circle cx="193" cy="325" r="37" fill="#fff" stroke="url(#arcCover)" stroke-width="2.5"/>
  </svg>

  <h1 class="cover-title">YOUR PERSONAL CARE<br>JOURNEY</h1>
  <p class="cover-intro">This booklet is designed to guide you through your care, help you understand your body, and support you in achieving long-term health and wellbeing.</p>
  <div class="field" style="left:65px;top:443px">Patient Name: <span class="blank" style="width:78px;margin-left:8px"></span></div>
  <div class="field" style="left:215px;top:443px">Date: <span class="blank" style="width:78px;margin-left:8px"></span></div>
  <div class="plan-pill">Your suggested care plan</div>
  <div class="field" style="left:122px;top:462px"><span class="blank" style="width:78px"></span> treatments over <span class="blank" style="width:62px;margin-left:6px"></span> &nbsp;weeks</div>
  <div class="field" style="left:122px;top:478px">Review/Reassessment at: <span class="blank" style="width:62px;margin-left:6px"></span></div>
</section>

<!-- ROAD TO RECOVERY -->
<section class="page page--recovery">
  <svg class="fill" width="386" height="240" role="img" aria-label="Photo: chiropractor explaining a spine model to a young woman in a bright clinic">
    <defs>
      <linearGradient id="recPhoto" x1="0" y1="0" x2="1" y2="0">
        <stop offset="0" stop-color="#c9c9c6"/>
        <stop offset=".55" stop-color="#e3e0dc"/>
        <stop offset="1" stop-color="#d6d3d2"/>
      </linearGradient>
      <linearGradient id="arcRec" x1="0" x2="1">
        <stop offset="0" stop-color="#ef72b8"/>
        <stop offset=".5" stop-color="#ab92d6"/>
        <stop offset="1" stop-color="#6fb1e7"/>
      </linearGradient>
    </defs>
    <path d="M0,0 H386 V150 Q193,330 0,160 Z" fill="url(#recPhoto)"/>
    <path d="M0,164 Q193,336 386,154" fill="none" stroke="url(#arcRec)" stroke-width="4"/>
  </svg>

  <div class="chart-card">
    <div class="chart-band"></div>
    <div class="chart-band-title">ROAD TO RECOVER</div>
    <div class="chart-graphic" role="img" aria-label="Infographic: road to recovery chart showing healing, correction and maintenance phases rising over days, weeks, months and years"></div>
  </div>

  <p class="welcome-copy">At Fernwell Spine Studio Chiropractic &amp; Wellness Ashbrook, we offer personalised chiropractic care for adults and families who want to feel their best — whether that’s easing discomfort, improving movement, or supporting long-term wellbeing.</p>
  <p class="welcome-tagline">Align your body, elevate your wellbeing</p>

  <svg class="footer-band" viewBox="0 360 386 140" width="386" height="140">
    <defs>
      <linearGradient id="arcFootA" x1="0" x2="1">
        <stop offset="0" stop-color="#ef72b8"/><stop offset=".5" stop-color="#ab92d6"/><stop offset="1" stop-color="#6fb1e7"/>
      </linearGradient>
    </defs>
    <path d="M12,500 Q193,352 374,500 Z" fill="url(#arcFootA)"/>
    <path d="M24,500 Q193,366 362,500 Z" fill="var(--teal)"/>
  </svg>
  <div class="chat-badge"><svg width="22" height="22" viewBox="0 0 22 22"><path d="M6,7 h10 a1.5,1.5 0 0 1 1.5,1.5 v5 a1.5,1.5 0 0 1 -1.5,1.5 h-5 l-3,2.5 v-2.5 h-2 a1.5,1.5 0 0 1 -1.5,-1.5 v-5 A1.5,1.5 0 0 1 6,7 Z" fill="var(--teal)"/><circle cx="8.5" cy="11" r=".9" fill="#fff"/><circle cx="11" cy="11" r=".9" fill="#fff"/><circle cx="13.5" cy="11" r=".9" fill="#fff"/></svg></div>
  <div class="footer-title" style="top:461px">WE ENCOURAGE<br>YOU TO ASK QUESTIONS AT ANY TIME.</div>
  <div class="footer-line">Understanding your care builds confidence - and better results.</div>
</section>

<!-- FIRST VISIT -->
<section class="page page--first-visit">
  <svg class="fill" width="386" height="240" role="img" aria-label="Photo: chiropractor adjusting a patient lying on a treatment table in a clinic room">
    <defs>
      <linearGradient id="visitPhoto" x1="0" y1="0" x2="1" y2="1">
        <stop offset="0" stop-color="#e4e2df"/>
        <stop offset=".5" stop-color="#8d9094"/>
        <stop offset="1" stop-color="#d7d5d2"/>
      </linearGradient>
      <linearGradient id="arcVisit" x1="0" x2="1">
        <stop offset="0" stop-color="#ef72b8"/><stop offset=".5" stop-color="#ab92d6"/><stop offset="1" stop-color="#6fb1e7"/>
      </linearGradient>
    </defs>
    <path d="M0,0 H386 V135 Q193,300 0,141 Z" fill="url(#visitPhoto)"/>
    <path d="M0,146 Q193,312 386,138" fill="none" stroke="url(#arcVisit)" stroke-width="5"/>
  </svg>

  <h2 class="section-title" style="left:21px;top:227px">YOU ARE IN GOOD HANDS</h2>
  <p class="section-copy justify" style="left:21px;top:241px;width:163px">We take a thorough, personalised approach because lasting results come from understanding the real cause of your problem.</p>
  <p class="section-copy" style="left:21px;top:287px;width:170px">We are here to guide and support you every step of the way.</p>
  <h2 class="section-title" style="left:21px;top:322px;width:150px">WHAT HAPPENED IN YOUR FIRST VISIT?</h2>
  <p class="section-copy" style="left:21px;top:345px;width:175px">Your first appointment was designed to understand the full picture - not just your pain.</p>

  <div class="step-card" style="left:203px;top:257px"></div>
  <div class="step-icon" style="left:201px;top:266px"><svg width="24" height="24" viewBox="0 0 24 24"><circle cx="11" cy="11" r="4" fill="none" stroke="#fff" stroke-width="1.6"/><path d="M14,14 L17.5,17.5" stroke="#fff" stroke-width="1.8" stroke-linecap="round"/></svg></div>
  <div class="step-title" style="left:233px;top:263px">EXAMINATION</div>
  <p class="step-copy" style="left:233px;top:273px">We assessed your posture, movement, how your joints are functioning.</p>

  <div class="step-card" style="left:203px;top:318px"></div>
  <div class="step-icon" style="left:201px;top:328px"><svg width="24" height="24" viewBox="0 0 24 24"><path d="M7,12.5 L10.5,16 L17,8.5" fill="none" stroke="#fff" stroke-width="1.8" stroke-linecap="round" stroke-linejoin="round"/></svg></div>
  <div class="step-title" style="left:233px;top:324px">FINDINGS</div>
  <p class="step-copy" style="left:233px;top:334px">We identified the underlying causes of your problem - not just where it hurts.</p>

  <div class="step-card" style="left:21px;top:379px"></div>
  <div class="step-icon" style="left:21px;top:388px"><svg width="24" height="24" viewBox="0 0 24 24"><path d="M6.5,8 h11 v6.5 h-6 l-3,2.5 v-2.5 h-2 Z" fill="#fff"/></svg></div>
  <div class="step-title" style="left:53px;top:385px">CONSULTATION</div>
  <p class="step-copy" style="left:53px;top:395px">We discussed your symptoms, health history, lifestyle, and goals.</p>

  <div class="step-card" style="left:203px;top:379px"></div>
  <div class="step-icon" style="left:201px;top:388px"><svg width="24" height="24" viewBox="0 0 24 24"><rect x="8" y="6.5" width="8" height="11" rx="1" fill="none" stroke="#fff" stroke-width="1.5"/><path d="M10,10 h4 M10,12.5 h4 M10,15 h2.5" stroke="#fff" stroke-width="1"/></svg></div>
  <div class="step-title" style="left:233px;top:385px">RECOMMENDATIONS</div>
  <p class="step-copy" style="left:233px;top:395px">We explained your results and created a personalised care plan tailored to you.</p>

  <svg class="footer-band" viewBox="0 360 386 140" width="386" height="140">
    <defs>
      <linearGradient id="arcFootB" x1="0" x2="1">
        <stop offset="0" stop-color="#ef72b8"/><stop offset=".5" stop-color="#ab92d6"/><stop offset="1" stop-color="#6fb1e7"/>
      </linearGradient>
    </defs>
    <path d="M12,500 Q193,352 374,500 Z" fill="url(#arcFootB)"/>
    <path d="M24,500 Q193,366 362,500 Z" fill="var(--teal)"/>
  </svg>
  <div class="chat-badge"><svg width="22" height="22" viewBox="0 0 22 22"><path d="M6,7 h10 a1.5,1.5 0 0 1 1.5,1.5 v5 a1.5,1.5 0 0 1 -1.5,1.5 h-5 l-3,2.5 v-2.5 h-2 a1.5,1.5 0 0 1 -1.5,-1.5 v-5 A1.5,1.5 0 0 1 6,7 Z" fill="var(--teal)"/><circle cx="8.5" cy="11" r=".9" fill="#fff"/><circle cx="11" cy="11" r=".9" fill="#fff"/><circle cx="13.5" cy="11" r=".9" fill="#fff"/></svg></div>
  <div class="footer-title" style="top:461px">WE ENCOURAGE<br>YOU TO ASK QUESTIONS AT ANY TIME.</div>
  <div class="footer-line">Understanding your care builds confidence - and better results.</div>
</section>

<!-- CONTINUING CARE -->
<section class="page page--continuing">
  <h2 class="section-title" style="left:27px;top:18px">WHY CONTINUING CARE MATTERS</h2>
  <p class="section-copy justify" style="left:27px;top:32px;width:152px;font-size:7.3px;line-height:10.5px">Pain often improves before the body is fully healed.</p>
  <div class="strong-line" style="left:27px;top:56px">Stopping care too early can lead to:</div>
  <ul class="bullets" style="left:37px;top:69px">
    <li>Symptoms returning</li>
    <li>Incomplete healing</li>
    <li>Ongoing underlying problems</li>
  </ul>
  <p class="section-copy" style="left:27px;top:111px;font-size:7.3px">Consistency is what creates lasting results.</p>

  <h2 class="section-title" style="left:207px;top:18px">YOUR ROLE IN YOUR RESULTS</h2>
  <p class="section-copy" style="left:207px;top:32px;font-size:7.3px">The best outcomes come from working together.</p>
  <div class="strong-line" style="left:207px;top:45px">To get the most from your care:</div>
  <ul class="bullets" style="left:217px;top:63px">
    <li>Attend your scheduled appointments</li>
    <li>Follow your exercises and advice</li>
    <li>Stay consistent with your plan</li>
    <li>Let us know how you’re progressing</li>
  </ul>

  <div class="abs" role="img" aria-label="Photo: practitioner pointing to a spine and pelvis model beside a patient" style="left:0;top:250px;width:386px;height:250px;background:linear-gradient(135deg,#e8e6e3 0%,#c9c3bd 45%,#6d7480 100%)"></div>

  <div class="journey-pill">
    <h2 class="journey-title">YOUR RECOMMENDED CARE JOURNEY</h2>
    <p class="journey-sub">Your care is structured in phases to give you the best long-term results.</p>
    <div class="phase" style="left:46px">
      <div class="phase-icon"><svg width="16" height="16" viewBox="0 0 16 16"><path d="M8,2 v12 M5,5 h6 M5,8 h6 M5,11 h6" stroke="#a98fd3" stroke-width="1.6" stroke-linecap="round"/></svg></div>
      <div class="phase-name">Phase 1: Relief</div>
      <div class="phase-focus">Short-term focus</div>
      <p class="phase-copy">Sed ut perspiciatis unde omnis<br>iste natus error sit voluptatem<br>accusan tium dolorem</p>
    </div>
    <div class="phase" style="left:145px">
      <div class="phase-icon"><svg width="16" height="16" viewBox="0 0 16 16"><path d="M8,13.5 C2,9.5 2,4 5.2,4 C6.7,4 7.6,5 8,6 C8.4,5 9.3,4 10.8,4 C14,4 14,9.5 8,13.5 Z" fill="#ef72b8"/></svg></div>
      <div class="phase-name">Phase 2: Restore</div>
      <div class="phase-focus">Mid-term focus</div>
      <p class="phase-copy">Sed ut perspiciatis unde omnis<br>iste natus error sit voluptatem<br>accusan tium dolorem</p>
    </div>
    <div class="phase" style="left:243px">
      <div class="phase-icon"><svg width="16" height="16" viewBox="0 0 16 16"><path d="M8,3 v10 M3,8 h10" stroke="#6fb1e7" stroke-width="2" stroke-linecap="round"/></svg></div>
      <div class="phase-name">Phase 3: Thrive</div>
      <div class="phase-focus">Long-term focus</div>
      <p class="phase-copy">Sed ut perspiciatis unde omnis<br>iste natus error sit voluptatem<br>accusan tium dolorem</p>
    </div>
  </div>

  <svg class="footer-band" viewBox="0 360 386 140" width="386" height="140">
    <defs>
      <linearGradient id="arcFootC" x1="0" x2="1">
        <stop offset="0" stop-color="#ef72b8"/><stop offset=".5" stop-color="#ab92d6"/><stop offset="1" stop-color="#6fb1e7"/>
      </linearGradient>
    </defs>
    <path d="M12,500 Q193,352 374,500 Z" fill="url(#arcFootC)"/>
    <path d="M24,500 Q193,366 362,500 Z" fill="var(--teal)"/>
  </svg>
  <div class="chat-badge"><svg width="22" height="22" viewBox="0 0 22 22"><path d="M6,7 h10 a1.5,1.5 0 0 1 1.5,1.5 v5 a1.5,1.5 0 0 1 -1.5,1.5 h-5 l-3,2.5 v-2.5 h-2 a1.5,1.5 0 0 1 -1.5,-1.5 v-5 A1.5,1.5 0 0 1 6,7 Z" fill="var(--teal)"/><circle cx="8.5" cy="11" r=".9" fill="#fff"/><circle cx="11" cy="11" r=".9" fill="#fff"/><circle cx="13.5" cy="11" r=".9" fill="#fff"/></svg></div>
  <div class="footer-title" style="top:461px">WE ENCOURAGE<br>YOU TO ASK QUESTIONS AT ANY TIME.</div>
  <div class="footer-line">Understanding your care builds confidence - and better results.</div>
</section>

</body>
</html>
```